Business Card Design

I need business cards designed for a new company i have started that makes cakes, particularly themed kids cakes with a really modern design and I would like to have my business cards reflect this. I have attached some photos of cakes I have made and would like some to be used.

Industry/Entity Type

Business

Contact Information for Business Card

Business Name: Tarts and Treats by Maren
Mobile: 0492 815 063
email: maren@tartsandtreatsbymaren.example.au
Instagram: instagram.com/tartsandtreatsbymaren/
Facebook: fb.me/tartsandtreatsbymaren

Colors
e667a6
b768aa
3276b5

Requirements
Must have
• Business Name: Tarts and Treats by Maren
• Mobile: 0492 815 063
• email: maren@tartsandtreatsbymaren.example.au
• Instagram: instagram.com/tartsandtreatsbymaren/
• Facebook: fb.me/tartsandtreatsbymaren
Nice to have
• 2 to 3 pictures of my cakes

```html
<!DOCTYPE html>
<html lang="en">
<head>
<meta charset="utf-8">
<title>Tarts and Treats by Maren – Business Card</title>
<link rel="stylesheet" href="https://fonts.googleapis.com/css2?family=Open+Sans:wght@400;600&display=swap">
<style>
  :root {
    --page-bg: #e8e3de;
    --frost: #eef0f1;
    --frost-edge: #dfe3e6;
    --pink-deep: #c9266f;
    --pink-mid: #e0508f;
    --pink-light: #e667a6;
    --ring: #8a2c6c;
    --brand: #a8216a;
    --text-light: #fbeaf2;
    --badge: #ffffff;
  }
  html, body {
    margin: 0;
    width: 1200px;
    height: 969px;
    overflow: hidden;
    background: var(--page-bg);
    font-family: "Open Sans", Arial, sans-serif;
  }
  .card {
    position: absolute;
    left: 100px;
    top: 200px;
    width: 1000px;
    height: 569px;
    border-radius: 20px;
    overflow: hidden;
    box-shadow: 0 10px 30px rgba(80, 50, 60, 0.18);
  }
  .card-art {
    position: absolute;
    inset: 0;
  }
  .holder {
    position: absolute;
    left: 52px;
    top: 50px;
    color: var(--text-light);
  }
  .holder-name {
    margin: 0;
    font-size: 30px;
    font-weight: 600;
    letter-spacing: 0.5px;
    line-height: 1.2;
  }
  .holder-role {
    margin: 4px 0 0;
    font-size: 25px;
    font-weight: 400;
  }
  .contacts {
    position: absolute;
    left: 52px;
    top: 380px;
    margin: 0;
    padding: 0;
    list-style: none;
    color: var(--text-light);
    font-size: 19px;
  }
  .contacts li {
    display: flex;
    align-items: center;
    height: 36px;
    white-space: nowrap;
  }
  .contacts svg {
    width: 20px;
    height: 20px;
    margin-right: 14px;
    flex: none;
  }
  .brand {
    position: absolute;
    left: 569px;
    top: 120px;
    width: 328px;
    height: 328px;
    border-radius: 50%;
    background: var(--badge);
    display: flex;
    align-items: center;
    justify-content: center;
    text-align: center;
  }
  .brand-name {
    margin: 0;
    color: var(--brand);
    font-size: 40px;
    font-weight: 600;
    line-height: 1.15;
  }
</style>
</head>
<body>
  <article class="card">
    <svg class="card-art" viewBox="0 0 1000 569" width="1000" height="569" aria-hidden="true">
      <defs>
        <linearGradient id="pink-panel" x1="0" y1="0" x2="1" y2="1">
          <stop offset="0" stop-color="var(--pink-deep)"/>
          <stop offset="0.5" stop-color="var(--pink-mid)"/>
          <stop offset="1" stop-color="var(--pink-light)"/>
        </linearGradient>
        <radialGradient id="frost-fill" cx="0.5" cy="0.5" r="0.6">
          <stop offset="0" stop-color="#f6f7f8"/>
          <stop offset="1" stop-color="var(--frost-edge)"/>
        </radialGradient>
      </defs>
      <rect class="card-base" width="1000" height="569" fill="var(--frost)"/>
      <rect class="pink-panel" width="716" height="569" fill="url(#pink-panel)"/>
      <circle class="feature-circle" cx="733" cy="284" r="293" fill="url(#frost-fill)"/>
      <circle class="feature-ring" cx="733" cy="284" r="306" fill="none" stroke="var(--ring)" stroke-width="3"/>
    </svg>

    <header class="holder">
      <h1 class="holder-name">JONAH PELL</h1>
      <p class="holder-role">CEO/Founder</p>
    </header>

    <ul class="contacts">
      <li>
        <svg viewBox="0 0 24 24" aria-hidden="true"><rect x="6" y="1" width="12" height="22" rx="2.5" fill="none" stroke="currentColor" stroke-width="2"/><circle cx="12" cy="19" r="1.3" fill="currentColor"/></svg>
        0492 815 063
      </li>
      <li>
        <svg viewBox="0 0 24 24" aria-hidden="true"><rect x="3" y="3" width="18" height="18" rx="3" fill="currentColor"/></svg>
        tartsandtreatsbymaren
      </li>
      <li>
        <svg viewBox="0 0 24 24" aria-hidden="true"><rect x="3" y="3" width="18" height="18" rx="3" fill="currentColor"/></svg>
        tartsandtreatsbymaren
      </li>
      <li>
        <svg viewBox="0 0 24 24" aria-hidden="true"><rect x="2" y="5" width="20" height="14" rx="1.5" fill="currentColor"/><path d="M3 6 L12 13 L21 6" fill="none" stroke="var(--pink-mid)" stroke-width="1.8"/></svg>
        maren@tartsandtreatsbymaren.example.au
      </li>
    </ul>

    <div class="brand">
      <p class="brand-name">Tarts<br>and Treats<br>by Maren</p>
    </div>
  </article>
</body>
</html>
```